Heritage Hollow Business Cards

Require a business card design. <br/><br/>Needs to include logo (either round or long version) plus these details:<br/>Maya Torvell<br/>Heritage Hollow<br/>maya@kelvadtrading.com.au<br/>02 6481 7395<br/>PO Box Glenwarra NSW 2791<br/>www.heritagehollow.com.au<br/><br/>I need in an editable format so that I can create for multiple staff members. <br/><br/>

Target Market(s)

We are an online store selling renovation products to home owners are builders. Looking for a classic classy design.

Industry/Entity Type

Home And Garden

Contact Information for Business Card

Maya Torvell
Heritage Hollow
maya@kelvadtrading.com.au
02 6481 7395
PO Box Glenwarra NSW 2791
www.heritagehollow.com.au

Colors

Designer to choose colors to be used in the design.

Requirements
Must have
• Must include Logo.

```html
<!DOCTYPE html>
<html lang="en">
<head>
<meta charset="utf-8">
<title>Heritage Hollow Business Cards</title>
<link rel="stylesheet" href="https://fonts.googleapis.com/css2?family=Arimo:wght@400;700&family=Rosarivo&display=swap">
<style>
  :root {
    --backdrop: #a3a3a3;
    --card-white: #ffffff;
    --card-black: #231f20;
    --ink: #1a1a1a;
    --logo-grey: #d9d9d9;
    --sketch-dark: #3a3a3a;
    --sketch-light: #8a8a8a;
  }
  * { margin: 0; padding: 0; box-sizing: border-box; }
  html, body { width: 1200px; height: 802px; overflow: hidden; }
  body {
    background: var(--backdrop);
    position: relative;
    font-family: "Arimo", Arial, sans-serif;
  }
  .card {
    position: absolute;
    top: 274px;
    width: 443px;
    height: 264px;
    overflow: hidden;
  }
  .card-front { left: 136px; background: var(--card-white); color: var(--ink); }
  .card-back { left: 624px; background: var(--card-black); }

  .roof-sketch { position: absolute; inset: 0; }

  .holder-name {
    position: absolute; left: 23px; top: 51px;
    font-weight: 700; font-size: 14.5px; letter-spacing: 0.3px;
  }
  .contact-list {
    position: absolute; left: 23px; top: 82px;
    list-style: none; font-size: 11.5px; line-height: 16.5px;
  }
  .contact-list li { display: flex; align-items: center; gap: 3px; }
  .contact-list svg { width: 12px; height: 12px; flex: none; }
  .postal-address {
    position: absolute; left: 23px; top: 144px;
    font-size: 11.5px; line-height: 15.5px; font-style: normal;
  }
  .brand-name {
    position: absolute; left: 0; right: 0; top: 142px;
    text-align: center; padding-left: 60px;
    font-family: "Rosarivo", Georgia, serif;
    font-size: 29px; color: var(--logo-grey); letter-spacing: 0.5px;
  }
</style>
</head>
<body>
  <section class="card card-front">
    <svg class="roof-sketch" viewBox="0 0 443 264" role="img" aria-label="Hand-sketched roof gable illustration">
      <defs>
        <linearGradient id="sketchTone" x1="0" y1="1" x2="1" y2="0">
          <stop offset="0" stop-color="var(--sketch-light)"/>
          <stop offset="1" stop-color="var(--sketch-dark)"/>
        </linearGradient>
      </defs>
      <polygon points="64,264 443,0 443,264" fill="url(#sketchTone)" opacity="0.85"/>
    </svg>
    <h1 class="holder-name">MAYA TORVELL</h1>
    <ul class="contact-list">
      <li>
        <svg viewBox="0 0 12 12"><rect x="0.6" y="0.6" width="10.8" height="10.8" rx="1.5" fill="none" stroke="currentColor" stroke-width="1"/><path d="M3.6 2.6c-.7.3-1 1-.6 1.9.8 1.8 2 3 3.7 3.8.9.4 1.6.1 1.9-.6l-1.3-1-.8.5c-.9-.5-1.5-1.1-2-2l.5-.8z" fill="currentColor"/></svg>
        02 6481 7395
      </li>
      <li>
        <svg viewBox="0 0 12 12"><path d="M0.5 2.5h11v7.5h-11z" fill="currentColor"/><path d="M0.8 2.8l5.2 4 5.2-4" fill="none" stroke="#fff" stroke-width="0.9"/></svg>
        maya@kelvadtrading.com.au
      </li>
      <li>
        <svg viewBox="0 0 12 12"><circle cx="6" cy="6" r="5.4" fill="currentColor"/><g fill="none" stroke="#fff" stroke-width="0.7"><ellipse cx="6" cy="6" rx="2.3" ry="5.2"/><path d="M0.8 6h10.4M1.6 3.3h8.8M1.6 8.7h8.8M6 0.7v10.6"/></g></svg>
        www.heritagehollow.com.au
      </li>
    </ul>
    <address class="postal-address">PO Box Glenwarra<br>NSW 2791</address>
  </section>

  <section class="card card-back">
    <p class="brand-name">Heritage Hollow</p>
  </section>
</body>
</html>
```